Corporate Trainning business needs PPT template for sales, reports and projects

Create a power point template with own design and rich in distinctness of our brand, logo and industry (corporate training). Enough slides templates to use for sales, reports and projects development: flowcharts, roadmaps, bullets, service categories, description box, title & subtitle slides, bar & pie charts, calendars, gantt, some basic shapes and icons (training, education, elearning, etc related).
Enclose: color palette, set of logo for different uses and ppt presentation with some ideas and slide templates. The ppt hope could help, but I trust in your experience and creativity.

Target Market(s)

Company training

Industry/Entity Type

Training - Education

Font styles to use
Sans Serif

Requirements
Nice to have
• Relative to training icons

```html
<!DOCTYPE html>
<html lang="en">
<head>
<meta charset="utf-8">
<title>Solvexa Presentation Template</title>
<link href="https://fonts.googleapis.com/css2?family=Montserrat:ital,wght@0,300;0,400;0,500;0,600;0,700;0,800;1,400&display=swap" rel="stylesheet">
<style>
:root{
  --navy:#10305c;
  --yellow:#f2c500;
  --teal:#1a93b3;
  --teal-light:#7cc4d8;
  --grey:#6b6f73;
  --paper:#ffffff;
  --panel:#f3f4f6;
  --stage:#e7e9ec;
  --ink:#2b2f36;
  --muted:#8a8f96;
  --ok:#2fa84f;
  --no:#d8322c;
}
*{margin:0;padding:0;box-sizing:border-box}
html,body{width:685px;height:1200px;overflow:hidden}
body{position:relative;background:linear-gradient(180deg,#dfe2e6 0%,var(--stage) 35%,#eef0f2 100%);font-family:'Montserrat',sans-serif;color:var(--ink)}
.brand-mark{position:absolute;left:516px;top:34px;display:flex;align-items:center;gap:8px;font-size:36px;font-weight:500;color:var(--navy);letter-spacing:-.5px}
.brand-mark .dot{width:26px;height:26px;border-radius:50%;background:var(--yellow)}
.slide{position:absolute;width:454px;height:255px;overflow:hidden;background:var(--paper);transform-origin:0 0;transform:scale(.4714)}
.slide.hero{transform:scale(1.013);box-shadow:0 10px 30px rgba(16,48,92,.18)}
.abs{position:absolute}
/* title slide */
.ts-photo{position:absolute;left:210px;top:0;width:244px;height:238px;border-radius:120px 0 0 120px/238px 0 0 0;background:linear-gradient(135deg,#c7d2dc 0%,#e9eef2 45%,#f6f3ee 70%,#d8c9b8 100%)}
.ts-accent{position:absolute;left:415px;top:132px;width:45px;height:72px;border-radius:18px;background:var(--yellow);opacity:.9}
.ts-logo{position:absolute;left:24px;top:24px;display:flex;align-items:center;gap:5px;font-size:20px;font-weight:500;color:var(--navy)}
.ts-logo .dot{width:14px;height:14px;border-radius:50%;background:var(--yellow)}
.ts-band{position:absolute;left:0;top:80px;width:252px;height:96px;border-radius:0 30px 30px 0;padding:14px 0 0 25px}
.ts-band .kicker{font-size:21px;font-weight:800;letter-spacing:.3px;line-height:1}
.ts-band .title{font-size:22px;font-weight:400;line-height:1.25}
.ts-band .sub{font-size:8px;font-weight:500;margin-top:5px}
.band-navy{background:var(--navy)} .band-navy .kicker,.band-navy .title{color:var(--yellow)} .band-navy .sub{color:#fff}
.band-yellow{background:var(--yellow)} .band-yellow .kicker,.band-yellow .title,.band-yellow .sub{color:var(--navy)}
.band-teal{background:var(--teal)} .band-teal .kicker,.band-teal .title,.band-teal .sub{color:#fff}
.ts-date{position:absolute;left:24px;top:205px;font-size:5.5px;color:var(--grey)}
.ts-foot{position:absolute;left:0;bottom:0;width:100%;height:17px;color:#fff;font-size:4.5px;text-align:center;line-height:17px}
/* content slides */
.head{position:absolute;left:18px;top:17px;display:flex;align-items:center;gap:10px;font-size:14px;color:var(--navy)}
.head::before{content:"";width:5px;height:19px;border-radius:3px;background:var(--yellow)}
.head b{font-weight:700}
.head.on-dark{color:#fff}
.foot-brand{position:absolute;left:12px;top:226px;display:flex;align-items:center;gap:4px;font-size:13px;font-weight:500;color:var(--navy)}
.foot-brand .dot{width:9px;height:9px;border-radius:50%;background:var(--yellow)}
.foot-brand.on-dark{color:#fff}
.foot-copy{position:absolute;right:32px;top:236px;font-size:4px;color:var(--muted)}
.foot-page{position:absolute;right:12px;top:233px;font-size:4.5px;color:var(--yellow);border-left:1.5px solid var(--teal);padding-left:5px;height:8px;line-height:8px}
.ico{position:absolute;border-radius:50%;display:flex;align-items:center;justify-content:center}
.ico svg{width:55%;height:55%}
.navy{background:var(--navy)} .yellow{background:var(--yellow)} .teal{background:var(--teal)}
.h9{font-size:9px;color:var(--ink)} .h9 b{font-weight:700}
.body5{font-size:4.8px;line-height:1.35;color:var(--muted)}
.center{text-align:center}
.photo{position:absolute}
</style>
</head>
<body>

<div class="brand-mark"><span class="dot"></span>Solvexa</div>

<!-- hero title slide -->
<div class="slide hero" style="left:60px;top:88px">
  <div class="ts-photo" role="img" aria-label="Photo of a hand drawing a line chart with a pen"></div>
  <div class="ts-accent"></div>
  <div class="ts-logo"><span class="dot"></span>Solvexa</div>
  <div class="ts-band band-yellow"><div class="kicker">PRESENTATION</div><div class="title">Title Goes Here!</div><div class="sub">Presentation Subtitle Goes Here!</div></div>
  <div class="ts-date">Monday, August 15, 2022</div>
  <div class="ts-foot navy">© 2022 Solvexa. All rights reserved.</div>
</div>

<!-- row 1: title variants -->
<div class="slide" style="left:15px;top:425px">
  <div class="ts-photo" role="img" aria-label="Photo of a hand drawing a line chart with a pen"></div>
  <div class="ts-accent"></div>
  <div class="ts-logo"><span class="dot"></span>Solvexa</div>
  <div class="ts-band band-navy"><div class="kicker">PRESENTATION</div><div class="title">Title Goes Here!</div><div class="sub">Presentation Subtitle Goes Here!</div></div>
  <div class="ts-date">Monday, August 15, 2022</div>
  <div class="ts-foot teal">© 2022 Solvexa. All rights reserved.</div>
</div>
<div class="slide" style="left:236px;top:425px">
  <div class="ts-photo" role="img" aria-label="Photo of a hand drawing a line chart with a pen"></div>
  <div class="ts-accent"></div>
  <div class="ts-logo"><span class="dot"></span>Solvexa</div>
  <div class="ts-band band-yellow"><div class="kicker">PRESENTATION</div><div class="title">Title Goes Here!</div><div class="sub">Presentation Subtitle Goes Here!</div></div>
  <div class="ts-date">Monday, August 15, 2022</div>
  <div class="ts-foot navy">© 2022 Solvexa. All rights reserved.</div>
</div>
<div class="slide" style="left:456px;top:425px">
  <div class="ts-photo" role="img" aria-label="Photo of a hand drawing a line chart with a pen"></div>
  <div class="ts-accent"></div>
  <div class="ts-logo"><span class="dot"></span>Solvexa</div>
  <div class="ts-band band-teal"><div class="kicker">PRESENTATION</div><div class="title">Title Goes Here!</div><div class="sub">Presentation Subtitle Goes Here!</div></div>
  <div class="ts-date">Monday, August 15, 2022</div>
  <div class="ts-foot navy">© 2022 Solvexa. All rights reserved.</div>
</div>

<!-- row 2 -->
<div class="slide" style="left:15px;top:552px">
  <div class="head"><span><b>Solvexa</b> Solutions</span></div>
  <div class="ico navy" style="left:72px;top:58px;width:30px;height:30px"><svg viewBox="0 0 10 10"><circle cx="5" cy="4" r="3" fill="#fff"/><rect x="4" y="7" width="2" height="2" fill="#fff"/></svg></div>
  <div class="ico yellow" style="left:212px;top:58px;width:30px;height:30px"><svg viewBox="0 0 10 10"><path d="M2 8 L8 2 L7 6 Z" fill="#fff"/></svg></div>
  <div class="ico teal" style="left:352px;top:58px;width:30px;height:30px"><svg viewBox="0 0 10 10"><circle cx="4.5" cy="4.5" r="2.6" fill="none" stroke="#fff" stroke-width="1.2"/><path d="M6.5 6.5 L9 9" stroke="#fff" stroke-width="1.3"/></svg></div>
  <div class="ico teal" style="left:72px;top:136px;width:30px;height:30px"><svg viewBox="0 0 10 10"><circle cx="5" cy="5" r="3.8" fill="none" stroke="#fff" stroke-width="1"/><path d="M5 2.6V5h2" stroke="#fff" stroke-width="1" fill="none"/></svg></div>
  <div class="ico navy" style="left:212px;top:136px;width:30px;height:30px"><svg viewBox="0 0 10 10"><circle cx="3" cy="4" r="1.4" fill="#fff"/><circle cx="7" cy="4" r="1.4" fill="#fff"/><circle cx="5" cy="3.4" r="1.6" fill="#fff"/><path d="M1 8c0-2 8-2 8 0z" fill="#fff"/></svg></div>
  <div class="ico yellow" style="left:352px;top:136px;width:30px;height:30px"><svg viewBox="0 0 10 10"><rect x="2" y="6" width="1.5" height="2.5" fill="#fff"/><rect x="4.3" y="4" width="1.5" height="4.5" fill="#fff"/><rect x="6.6" y="2" width="1.5" height="6.5" fill="#fff"/></svg></div>
  <div class="abs center" style="left:27px;top:92px;width:120px"><div class="h9"><b>Heading</b> Goes Here</div><div class="body5">Short note on this point.</div></div>
  <div class="abs center" style="left:167px;top:92px;width:120px"><div class="h9"><b>Heading</b> Goes Here</div><div class="body5">Short note on this point.</div></div>
  <div class="abs center" style="left:307px;top:92px;width:120px"><div class="h9"><b>Heading</b> Goes Here</div><div class="body5">Short note on this point.</div></div>
  <div class="abs center" style="left:27px;top:170px;width:120px"><div class="h9"><b>Heading</b> Goes Here</div><div class="body5">Short note on this point.</div></div>
  <div class="abs center" style="left:167px;top:170px;width:120px"><div class="h9"><b>Heading</b> Goes Here</div><div class="body5">Short note on this point.</div></div>
  <div class="abs center" style="left:307px;top:170px;width:120px"><div class="h9"><b>Heading</b> Goes Here</div><div class="body5">Short note on this point.</div></div>
  <div class="foot-brand"><span class="dot"></span>Solvexa</div><div class="foot-copy">© 2022 Solvexa. All rights reserved.</div><div class="foot-page">4</div>
</div>

<div class="slide" style="left:236px;top:552px">
  <div class="head"><span><b>Solvexa</b> Values</span></div>
  <div class="ico navy" style="left:62px;top:54px;width:38px;height:38px"><svg viewBox="0 0 10 10"><path d="M4 1.5h2v3l2.5 4h-7L4 4.5z" fill="#fff"/></svg></div>
  <div class="ico yellow" style="left:62px;top:106px;width:38px;height:38px"><svg viewBox="0 0 10 10"><circle cx="5" cy="4" r="3" fill="#fff"/><rect x="4.5" y="6" width="1" height="3" fill="#fff"/></svg></div>
  <div class="ico teal" style="left:62px;top:158px;width:38px;height:38px"><svg viewBox="0 0 10 10"><path d="M2 8 L8 2 L7 6 Z" fill="#fff"/></svg></div>
  <div class="abs" style="left:110px;top:57px;width:290px"><div class="h9">we love <b>innovations</b></div><div class="body5">A short line of supporting text goes here for this value and what it means to the team today.</div></div>
  <div class="abs" style="left:110px;top:109px;width:290px"><div class="h9">we respect the <b>nature</b></div><div class="body5">A short line of supporting text goes here for this value and what it means to the team today.</div></div>
  <div class="abs" style="left:110px;top:161px;width:290px"><div class="h9">we believe in <b>future</b></div><div class="body5">A short line of supporting text goes here for this value and what it means to the team today.</div></div>
  <div class="foot-brand"><span class="dot"></span>Solvexa</div><div class="foot-copy">© 2022 Solvexa. All rights reserved.</div><div class="foot-page">5</div>
</div>

<div class="slide" style="left:456px;top:552px">
  <div class="abs navy" style="left:0;top:0;width:228px;height:255px"></div>
  <div class="photo" style="left:235px;top:7px;width:212px;height:220px;background:linear-gradient(140deg,#5b6f86 0%,#2d3d52 55%,#b9c4cf 100%)" role="img" aria-label="Photo of hands holding a tablet showing a stock chart"></div>
  <div class="head on-dark"><span><b>Heading</b> Goes Here!</span></div>
  <div class="ico yellow" style="left:34px;top:60px;width:26px;height:26px"><svg viewBox="0 0 10 10"><rect x="2.5" y="4.5" width="5" height="4" fill="#fff"/><path d="M3.5 4.5V3a1.5 1.5 0 013 0v1.5" stroke="#fff" fill="none"/></svg></div>
  <div class="ico yellow" style="left:34px;top:98px;width:26px;height:26px"><svg viewBox="0 0 10 10"><rect x="2" y="6" width="1.5" height="2.5" fill="#fff"/><rect x="4.3" y="4" width="1.5" height="4.5" fill="#fff"/><rect x="6.6" y="2" width="1.5" height="6.5" fill="#fff"/></svg></div>
  <div class="ico yellow" style="left:34px;top:136px;width:26px;height:26px"><svg viewBox="0 0 10 10"><circle cx="5" cy="5" r="3.8" fill="none" stroke="#fff"/><path d="M5 2.6V5h2" stroke="#fff" fill="none"/></svg></div>
  <div class="ico yellow" style="left:34px;top:174px;width:26px;height:26px"><svg viewBox="0 0 10 10"><rect x="2.5" y="4.5" width="5" height="4" fill="#fff"/><path d="M3.5 4.5V3a1.5 1.5 0 013 0v1.5" stroke="#fff" fill="none"/></svg></div>
  <div class="abs" style="left:70px;top:62px;width:140px"><div style="font-size:8px;color:var(--yellow)">Feature <b>One</b></div><div class="body5" style="color:#dfe6ef">Short note on this point.</div></div>
  <div class="abs" style="left:70px;top:100px;width:140px"><div style="font-size:8px;color:var(--yellow)">Feature <b>Two</b></div><div class="body5" style="color:#dfe6ef">Short note on this point.</div></div>
  <div class="abs" style="left:70px;top:138px;width:140px"><div style="font-size:8px;color:var(--yellow)">Feature <b>Three</b></div><div class="body5" style="color:#dfe6ef">Short note on this point.</div></div>
  <div class="abs" style="left:70px;top:176px;width:140px"><div style="font-size:8px;color:var(--yellow)">Feature <b>Four</b></div><div class="body5" style="color:#dfe6ef">Short note on this point.</div></div>
  <div class="foot-brand on-dark"><span class="dot"></span>Solvexa</div><div class="foot-copy">© 2022 Solvexa. All rights reserved.</div><div class="foot-page">6</div>
</div>

<!-- row 3 -->
<div class="slide" style="left:15px;top:680px">
  <div class="abs" style="left:228px;top:0;width:226px;height:255px;background:var(--panel)"></div>
  <div class="photo" style="left:7px;top:7px;width:213px;height:208px;background:linear-gradient(135deg,#8a6a4c 0%,#c9c6c0 40%,#eceae6 60%,#7a5a3e 100%)" role="img" aria-label="Top-down photo of a team working around a table with charts"></div>
  <div class="head" style="left:242px"><span>Four Steps <b>Process</b></span></div>
  <div class="abs" style="left:310px;top:66px;width:1.5px;height:122px;background:var(--navy)"></div>
  <div class="abs" style="left:262px;top:60px;width:170px">
    <div style="position:relative;height:40px"><span class="abs" style="left:0;top:0;font-size:6px;font-weight:700;color:var(--teal)">JUN 01</span><span class="abs" style="left:45.5px;top:2px;width:6px;height:6px;border-radius:50%;background:var(--navy)"></span><div class="abs" style="left:58px;top:-2px"><div class="h9"><b>Start</b> Point</div><div class="body5">Short note on this point.</div></div></div>
    <div style="position:relative;height:40px"><span class="abs" style="left:4px;top:0;font-size:6px;font-weight:700;color:var(--teal)">JUL 15</span><span class="abs" style="left:45.5px;top:2px;width:6px;height:6px;border-radius:50%;background:var(--navy)"></span><div class="abs" style="left:58px;top:-2px"><div class="h9"><b>Midpoint</b> One</div><div class="body5">Short note on this point.</div></div></div>
    <div style="position:relative;height:40px"><span class="abs" style="left:0;top:0;font-size:6px;font-weight:700;color:var(--teal)">AUG 01</span><span class="abs" style="left:45.5px;top:2px;width:6px;height:6px;border-radius:50%;background:var(--navy)"></span><div class="abs" style="left:58px;top:-2px"><div class="h9"><b>Midpoint</b> Two</div><div class="body5">Short note on this point.</div></div></div>
    <div style="position:relative;height:40px"><span class="abs" style="left:2px;top:0;font-size:6px;font-weight:700;color:var(--teal)">SEP 15</span><span class="abs" style="left:45.5px;top:2px;width:6px;height:6px;border-radius:50%;background:var(--navy)"></span><div class="abs" style="left:58px;top:-2px"><div class="h9"><b>Finish</b></div><div class="body5">Short note on this point.</div></div></div>
  </div>
  <div class="foot-brand"><span class="dot"></span>Solvexa</div><div class="foot-copy">© 2022 Solvexa. All rights reserved.</div><div class="foot-page">7</div>
</div>

<div class="slide" style="left:236px;top:680px">
  <div class="head"><span><b>Branding</b> Infographics</span></div>
  <div class="abs body5" style="left:33px;top:44px;width:130px">Branding is how people see and remember our training work.</div>
  <svg class="abs" style="left:130px;top:60px" width="200" height="160" viewBox="0 0 200 160">
    <circle cx="100" cy="52" r="46" fill="var(--navy)"/>
    <circle cx="72" cy="102" r="46" fill="var(--teal)" fill-opacity=".95"/>
    <circle cx="128" cy="102" r="46" fill="var(--yellow)" fill-opacity=".95"/>
    <path d="M100 52 m-2 40 a46 46 0 0 1 -26 -40" fill="none"/>
    <circle cx="100" cy="88" r="22" fill="#4a5a70"/>
    <text x="100" y="30" font-size="4.5" fill="#fff" text-anchor="middle" font-family="Montserrat">Visual Identity</text>
    <text x="52" y="112" font-size="4.5" fill="#fff" text-anchor="middle" font-family="Montserrat">Brand Tone</text>
    <text x="150" y="112" font-size="4.5" fill="#fff" text-anchor="middle" font-family="Montserrat">Strategy</text>
    <circle cx="70" cy="70" r="6" fill="none" stroke="#fff"/><circle cx="130" cy="70" r="6" fill="none" stroke="#fff"/><circle cx="100" cy="112" r="6" fill="none" stroke="#fff"/>
  </svg>
  <div class="abs" style="left:288px;top:74px;width:2px;height:18px;background:var(--navy)"></div><div class="abs body5" style="left:294px;top:74px;width:70px">Short note on this point.</div>
  <div class="abs" style="left:152px;top:150px;width:2px;height:18px;background:var(--teal)"></div><div class="abs body5" style="left:40px;top:152px;width:106px;text-align:right">Short note on this point.</div>
  <div class="abs" style="left:308px;top:150px;width:2px;height:18px;background:var(--yellow)"></div><div class="abs body5" style="left:314px;top:152px;width:70px">Short note on this point.</div>
  <div class="foot-brand"><span class="dot"></span>Solvexa</div><div class="foot-copy">© 2022 Solvexa. All rights reserved.</div><div class="foot-page">8</div>
</div>

<div class="slide" style="left:456px;top:680px">
  <div class="head"><span>Creative <b>Infographics</b></span></div>
  <svg class="abs" style="left:167px;top:75px" width="120" height="120" viewBox="0 0 120 120">
    <g transform="rotate(-90 60 60)" fill="none" stroke-width="26">
      <circle cx="60" cy="60" r="44" pathLength="100" stroke="var(--navy)" stroke-dasharray="32 68" stroke-dashoffset="-1"/>
      <circle cx="60" cy="60" r="44" pathLength="100" stroke="var(--yellow)" stroke-dasharray="31 69" stroke-dashoffset="-35"/>
      <circle cx="60" cy="60" r="44" pathLength="100" stroke="var(--teal)" stroke-dasharray="31 69" stroke-dashoffset="-68"/>
    </g>
  </svg>
  <div class="abs" style="left:300px;top:68px;width:110px"><div class="h9">Title <b>One</b></div><div class="body5">Short note on this point.</div></div>
  <div class="abs" style="left:300px;top:172px;width:110px"><div class="h9">Title <b>Two</b></div><div class="body5">Short note on this point.</div></div>
  <div class="abs" style="left:40px;top:84px;width:115px;text-align:right"><div class="h9">Title <b>Three</b></div><div class="body5">Short note on this point.</div></div>
  <div class="foot-brand"><span class="dot"></span>Solvexa</div><div class="foot-copy">© 2022 Solvexa. All rights reserved.</div><div class="foot-page">9</div>
</div>

<!-- row 4 -->
<div class="slide" style="left:15px;top:807px">
  <div class="head"><span>Creative <b>Infographics</b></span></div>
  <svg class="abs" style="left:172px;top:77px" width="110" height="110" viewBox="0 0 110 110">
    <g transform="rotate(-90 55 55)" fill="none" stroke-width="26">
      <circle cx="55" cy="55" r="40" pathLength="100" stroke="var(--navy)" stroke-dasharray="15.5 84.5" stroke-dashoffset="-0.5"/>
      <circle cx="55" cy="55" r="40" pathLength="100" stroke="var(--yellow)" stroke-dasharray="15.5 84.5" stroke-dashoffset="-17.2"/>
      <circle cx="55" cy="55" r="40" pathLength="100" stroke="var(--teal)" stroke-dasharray="15.5 84.5" stroke-dashoffset="-33.8"/>
      <circle cx="55" cy="55" r="40" pathLength="100" stroke="var(--navy)" stroke-dasharray="15.5 84.5" stroke-dashoffset="-50.5"/>
      <circle cx="55" cy="55" r="40" pathLength="100" stroke="var(--yellow)" stroke-dasharray="15.5 84.5" stroke-dashoffset="-67.2"/>
      <circle cx="55" cy="55" r="40" pathLength="100" stroke="var(--teal)" stroke-dasharray="15.5 84.5" stroke-dashoffset="-83.8"/>
    </g>
  </svg>
  <div class="abs" style="left:40px;top:78px;width:122px;text-align:right;border-right:2.5px solid var(--navy);padding-right:6px"><div class="h9"><b>Heading</b> Goes Here</div><div class="body5">Short note on this point.</div></div>
  <div class="abs" style="left:22px;top:122px;width:130px;text-align:right;border-right:2.5px solid var(--teal);padding-right:6px"><div class="h9"><b>Heading</b> Goes Here</div><div class="body5">Short note on this point.</div></div>
  <div class="abs" style="left:40px;top:166px;width:122px;text-align:right;border-right:2.5px solid var(--yellow);padding-right:6px"><div class="h9"><b>Heading</b> Goes Here</div><div class="body5">Short note on this point.</div></div>
  <div class="abs" style="left:292px;top:78px;width:122px;border-left:2.5px solid var(--yellow);padding-left:6px"><div class="h9"><b>Heading</b> Goes Here</div><div class="body5">Short note on this point.</div></div>
  <div class="abs" style="left:302px;top:122px;width:122px;border-left:2.5px solid var(--navy);padding-left:6px"><div class="h9"><b>Heading</b> Goes Here</div><div class="body5">Short note on this point.</div></div>
  <div class="abs" style="left:292px;top:166px;width:122px;border-left:2.5px solid var(--navy);padding-left:6px"><div class="h9"><b>Heading</b> Goes Here</div><div class="body5">Short note on this point.</div></div>
  <div class="foot-brand"><span class="dot"></span>Solvexa</div><div class="foot-copy">© 2022 Solvexa. All rights reserved.</div><div class="foot-page">10</div>
</div>

<div class="slide" style="left:236px;top:807px;background:var(--navy)">
  <div class="abs" style="inset:0;background:linear-gradient(120deg,rgba(26,147,179,.12),rgba(16,48,92,0) 60%)" role="img" aria-label="Faint photo of a hand drawing a chart, tinted navy"></div>
  <div class="abs yellow" style="left:53px;top:98px;width:94px;height:94px;border-radius:50%;display:flex;align-items:center;justify-content:center">
    <svg width="48" height="34" viewBox="0 0 48 34"><path d="M2 0h18v18l-8 16H4l6-14H2z M28 0h18v18l-8 16h-8l6-14h-8z" fill="#fff"/></svg>
  </div>
  <div class="abs" style="left:170px;top:120px;width:230px;color:#fff;font-size:7.2px;font-style:italic;line-height:1.3">“Great training turns daily work into steady growth for every team we serve and every person in it.”
    <div style="font-style:normal;margin-top:10px"><b>- John Doe</b> (someone)</div></div>
</div>

<div class="slide" style="left:456px;top:807px">
  <div class="head"><span><b>Customer Journey Infographics</b></span></div>
  <svg class="abs" style="left:20px;top:60px" width="420" height="44" viewBox="0 0 420 44">
    <polygon points="0,12 76,12 86,22 76,32 0,32 10,22" fill="var(--navy)"/>
    <polygon points="82,12 158,12 168,22 158,32 82,32 92,22" fill="var(--yellow)"/>
    <polygon points="164,12 240,12 250,22 240,32 164,32 174,22" fill="var(--teal)"/>
    <polygon points="246,12 322,12 332,22 322,32 246,32 256,22" fill="var(--teal-light)"/>
    <polygon points="328,12 404,12 414,22 404,32 328,32 338,22" fill="var(--grey)"/>
    <g stroke-width="3" fill="#fff">
      <circle cx="44" cy="22" r="15" stroke="var(--navy)"/><circle cx="126" cy="22" r="15" stroke="var(--yellow)"/><circle cx="208" cy="22" r="15" stroke="var(--teal)"/><circle cx="290" cy="22" r="15" stroke="var(--teal-light)"/><circle cx="372" cy="22" r="15" stroke="var(--grey)"/>
    </g>
    <circle cx="44" cy="20" r="5" fill="var(--navy)"/><circle cx="126" cy="22" r="5" fill="var(--yellow)"/><circle cx="208" cy="22" r="5" fill="var(--teal)"/><rect x="286" y="17" width="8" height="10" rx="2" fill="var(--teal-light)"/><path d="M366 18l6-3 6 3v7l-6 3-6-3z" fill="var(--grey)"/>
  </svg>
  <div class="abs center" style="left:24px;top:110px;width:80px"><div style="font-size:6.5px;font-weight:700;color:var(--ink)">Awareness</div><div class="body5" style="margin-top:6px">A short line of text about this stage of the journey.</div></div>
  <div class="abs center" style="left:106px;top:110px;width:80px"><div style="font-size:6.5px;font-weight:700;color:var(--ink)">Preferences</div><div class="body5" style="margin-top:6px">A short line of text about this stage of the journey.</div></div>
  <div class="abs center" style="left:188px;top:110px;width:80px"><div style="font-size:6.5px;font-weight:700;color:var(--ink)">Considerations</div><div class="body5" style="margin-top:6px">A short line of text about this stage of the journey.</div></div>
  <div class="abs center" style="left:270px;top:110px;width:80px"><div style="font-size:6.5px;font-weight:700;color:var(--ink)">Pre-Order</div><div class="body5" style="margin-top:6px">A short line of text about this stage of the journey.</div></div>
  <div class="abs center" style="left:352px;top:110px;width:80px"><div style="font-size:6.5px;font-weight:700;color:var(--ink)">Order</div><div class="body5" style="margin-top:6px">A short line of text about this stage of the journey.</div></div>
  <div class="foot-brand"><span class="dot"></span>Solvexa</div><div class="foot-copy">© 2022 Solvexa. All rights reserved.</div><div class="foot-page">12</div>
</div>

<!-- row 5 -->
<div class="slide" style="left:15px;top:934px">
  <div class="head"><span><b>Calendar</b></span></div>
  <div class="abs" style="left:48px;top:62px;width:104px;height:124px;background:var(--panel);border-radius:6px"></div>
  <div class="abs" style="left:168px;top:56px;width:118px;height:138px;background:#fff;border:1.5px solid #e1e3e6;border-radius:8px"></div>
  <div class="abs" style="left:302px;top:62px;width:104px;height:124px;background:var(--panel);border-radius:6px"></div>
  <div class="abs center" style="left:48px;top:68px;width:104px;font-size:4.5px;color:var(--muted);letter-spacing:1px">JULY</div>
  <div class="abs center" style="left:168px;top:62px;width:118px;font-size:4.5px;color:var(--muted);letter-spacing:1px">AUGUST</div>
  <div class="abs center" style="left:302px;top:68px;width:104px;font-size:4.5px;color:var(--muted);letter-spacing:1px">SEPTEMBER</div>
  <div class="abs navy center" style="left:62px;top:80px;width:76px;height:52px;border-radius:4px;color:#fff;padding-top:6px"><div style="font-size:20px;font-weight:700;line-height:1">03</div><div style="font-size:7px">Monday</div></div>
  <div class="abs yellow center" style="left:182px;top:74px;width:90px;height:60px;border-radius:4px;color:#fff;padding-top:8px"><div style="font-size:22px;font-weight:700;line-height:1">15</div><div style="font-size:8px">Tuesday</div></div>
  <div class="abs teal center" style="left:316px;top:80px;width:76px;height:52px;border-radius:4px;color:#fff;padding-top:6px"><div style="font-size:20px;font-weight:700;line-height:1">24</div><div style="font-size:7px">Friday</div></div>
  <div class="abs body5 center" style="left:62px;top:148px;width:76px">Short note on this point.</div>
  <div class="abs body5 center" style="left:182px;top:150px;width:90px">Short note on this point.</div>
  <div class="abs body5 center" style="left:316px;top:148px;width:76px">Short note on this point.</div>
  <div class="foot-brand"><span class="dot"></span>Solvexa</div><div class="foot-copy">© 2022 Solvexa. All rights reserved.</div><div class="foot-page">13</div>
</div>

<div class="slide" style="left:236px;top:934px">
  <div class="head"><span><b>E-Learning</b> Infographics</span></div>
  <div class="abs" style="left:20px;top:60px;width:205px;height:148px;border-radius:10px;background:linear-gradient(135deg,#eef3f7 0%,#dbe8ef 55%,#f7efc8 100%)" role="img" aria-label="Illustration of people around a large screen with charts and online lessons"></div>
  <div class="ico navy" style="left:256px;top:70px;width:28px;height:28px"><svg viewBox="0 0 10 10"><path d="M3 2h4v2a2 2 0 01-4 0z M4.5 6h1v1.5h1.5v1h-4v-1h1.5z" fill="#fff"/></svg></div>
  <div class="ico yellow" style="left:324px;top:70px;width:28px;height:28px"><svg viewBox="0 0 10 10"><circle cx="5" cy="3.6" r="1.8" fill="#fff"/><path d="M1.8 9c0-3 6.4-3 6.4 0z" fill="#fff"/></svg></div>
  <div class="ico teal" style="left:392px;top:70px;width:28px;height:28px"><svg viewBox="0 0 10 10"><circle cx="3" cy="4" r="1.4" fill="#fff"/><circle cx="7" cy="4" r="1.4" fill="#fff"/><circle cx="5" cy="3.4" r="1.6" fill="#fff"/><path d="M1 8c0-2 8-2 8 0z" fill="#fff"/></svg></div>
  <div class="abs center" style="left:240px;top:104px;width:60px"><div style="font-size:17px;font-weight:700;color:var(--navy)">20<span style="font-size:8px;font-weight:400">%</span></div><div style="font-size:6.5px;font-weight:700;margin-top:6px">Education</div><div class="body5" style="margin-top:4px">Short note on this point.</div></div>
  <div class="abs center" style="left:308px;top:104px;width:60px"><div style="font-size:17px;font-weight:700;color:var(--yellow)">45<span style="font-size:8px;font-weight:400">%</span></div><div style="font-size:6.5px;font-weight:700;margin-top:6px">Teachers</div><div class="body5" style="margin-top:4px">Short note on this point.</div></div>
  <div class="abs center" style="left:376px;top:104px;width:60px"><div style="font-size:17px;font-weight:700;color:var(--teal)">35<span style="font-size:8px;font-weight:400">%</span></div><div style="font-size:6.5px;font-weight:700;margin-top:6px">Students</div><div class="body5" style="margin-top:4px">Short note on this point.</div></div>
  <div class="foot-brand"><span class="dot"></span>Solvexa</div><div class="foot-copy">© 2022 Solvexa. All rights reserved.</div><div class="foot-page">14</div>
</div>

<div class="slide" style="left:456px;top:934px">
  <div class="head"><span><b>Table</b> Layout</span></div>
  <svg class="abs" style="left:30px;top:60px" width="396" height="140" viewBox="0 0 396 140" font-family="Montserrat">
    <rect x="0" y="0" width="80" height="20" fill="var(--navy)"/>
    <rect x="80" y="0" width="79" height="20" fill="var(--yellow)"/>
    <rect x="159" y="0" width="79" height="20" fill="var(--teal)"/>
    <rect x="238" y="0" width="79" height="20" fill="var(--teal-light)"/>
    <rect x="317" y="0" width="79" height="20" fill="var(--grey)"/>
    <text x="4" y="12.5" font-size="5" fill="#fff" font-weight="700">Heading</text>
    <g font-size="4.6" fill="#fff" text-anchor="middle" font-weight="600"><text x="119.5" y="12.5">Column Title 1</text><text x="198.5" y="12.5">Column Title 2</text><text x="277.5" y="12.5">Column Title 3</text><text x="356.5" y="12.5">Column Title 4</text></g>
    <g fill="#f6f7f8"><rect x="0" y="42" width="396" height="22"/><rect x="0" y="86" width="396" height="22"/></g>
    <g stroke="#e3e5e8" stroke-width=".6"><line x1="0" y1="42" x2="396" y2="42"/><line x1="0" y1="64" x2="396" y2="64"/><line x1="0" y1="86" x2="396" y2="86"/><line x1="0" y1="108" x2="396" y2="108"/><line x1="0" y1="130" x2="396" y2="130"/><line x1="80" y1="20" x2="80" y2="130"/><line x1="159" y1="20" x2="159" y2="130"/><line x1="238" y1="20" x2="238" y2="130"/><line x1="317" y1="20" x2="317" y2="130"/></g>
    <g font-size="5.5" font-weight="700" fill="var(--ink)"><text x="4" y="34">Feature One</text><text x="4" y="56">Feature Two</text><text x="4" y="78">Feature Three</text><text x="4" y="100">Feature Four</text><text x="4" y="122">Feature Five</text></g>
    <g font-size="8" text-anchor="middle" font-weight="700">
      <g fill="var(--ok)"><text x="119.5" y="35">✓</text><text x="198.5" y="35">✓</text><text x="277.5" y="35">✓</text><text x="356.5" y="35">✓</text>
      <text x="119.5" y="57">✓</text><text x="198.5" y="57">✓</text><text x="277.5" y="57">✓</text><text x="356.5" y="57">✓</text>
      <text x="119.5" y="79">✓</text><text x="198.5" y="79">✓</text><text x="277.5" y="79">✓</text>
      <text x="119.5" y="101">✓</text><text x="198.5" y="101">✓</text>
      <text x="119.5" y="123">✓</text></g>
      <g fill="var(--no)"><text x="356.5" y="79">✕</text><text x="277.5" y="101">✕</text><text x="356.5" y="101">✕</text><text x="198.5" y="123">✕</text><text x="277.5" y="123">✕</text><text x="356.5" y="123">✕</text></g>
    </g>
  </svg>
  <div class="foot-brand"><span class="dot"></span>Solvexa</div><div class="foot-copy">© 2022 Solvexa. All rights reserved.</div><div class="foot-page">15</div>
</div>

<!-- row 6 -->
<div class="slide" style="left:15px;top:1062px">
  <div class="head"><span><b>Circle</b> Infographics</span></div>
  <svg class="abs" style="left:52px;top:62px" width="350" height="100" viewBox="0 0 350 100" font-family="Montserrat">
    <g fill="none" stroke-width="6" transform="rotate(-90 48 50)"><circle cx="48" cy="50" r="42" stroke="#eef0f2"/><circle cx="48" cy="50" r="42" pathLength="100" stroke="var(--navy)" stroke-dasharray="64 100"/></g>
    <g fill="none" stroke-width="6" transform="rotate(-90 175 50)"><circle cx="175" cy="50" r="42" stroke="#eef0f2"/><circle cx="175" cy="50" r="42" pathLength="100" stroke="var(--yellow)" stroke-dasharray="82 100"/></g>
    <g fill="none" stroke-width="6" transform="rotate(-90 302 50)"><circle cx="302" cy="50" r="42" stroke="#eef0f2"/><circle cx="302" cy="50" r="42" pathLength="100" stroke="var(--teal)" stroke-dasharray="94 100"/></g>
    <g font-size="15" font-weight="700" text-anchor="middle"><text x="48" y="55" fill="var(--navy)">64%</text><text x="175" y="55" fill="var(--yellow)">82%</text><text x="302" y="55" fill="var(--teal)">94%</text></g>
  </svg>
  <div class="abs center" style="left:50px;top:168px;width:100px"><div style="font-size:8px;font-weight:700;color:var(--navy)">California</div><div class="body5">Short note on this point.</div></div>
  <div class="abs center" style="left:177px;top:168px;width:100px"><div style="font-size:8px;font-weight:700;color:var(--yellow)">Florida</div><div class="body5">Short note on this point.</div></div>
  <div class="abs center" style="left:304px;top:168px;width:100px"><div style="font-size:8px;font-weight:700;color:var(--teal)">New York</div><div class="body5">Short note on this point.</div></div>
  <div class="foot-brand"><span class="dot"></span>Solvexa</div><div class="foot-copy">© 2022 Solvexa. All rights reserved.</div><div class="foot-page">16</div>
</div>

<div class="slide" style="left:236px;top:1062px">
  <div class="head"><span><b>Chart</b> Slide</span></div>
  <svg class="abs" style="left:28px;top:70px" width="200" height="130" viewBox="0 0 200 130" font-family="Montserrat">
    <g stroke="#e6e8eb" stroke-width=".6"><line x1="20" y1="10" x2="200" y2="10"/><line x1="20" y1="27" x2="200" y2="27"/><line x1="20" y1="44" x2="200" y2="44"/><line x1="20" y1="61" x2="200" y2="61"/><line x1="20" y1="78" x2="200" y2="78"/><line x1="20" y1="95" x2="200" y2="95"/><line x1="20" y1="112" x2="200" y2="112"/></g>
    <g font-size="4" fill="var(--muted)" text-anchor="end"><text x="14" y="12">6</text><text x="14" y="29">5</text><text x="14" y="46">4</text><text x="14" y="63">3</text><text x="14" y="80">2</text><text x="14" y="97">1</text><text x="14" y="114">0</text></g>
    <rect x="30" y="39" width="6" height="73" fill="var(--navy)"/><rect x="38" y="71" width="6" height="41" fill="var(--yellow)"/><rect x="46" y="78" width="6" height="34" fill="var(--teal)"/>
    <rect x="72" y="54" width="6" height="58" fill="var(--navy)"/><rect x="80" y="36" width="6" height="76" fill="var(--yellow)"/><rect x="88" y="78" width="6" height="34" fill="var(--teal)"/>
    <rect x="114" y="51" width="6" height="61" fill="var(--navy)"/><rect x="122" y="88" width="6" height="24" fill="var(--yellow)"/><rect x="130" y="61" width="6" height="51" fill="var(--teal)"/>
    <rect x="156" y="27" width="6" height="85" fill="var(--navy)"/><rect x="164" y="64" width="6" height="48" fill="var(--yellow)"/><rect x="172" y="20" width="6" height="92" fill="var(--teal)"/>
    <g font-size="4" fill="var(--muted)" text-anchor="middle"><text x="41" y="122">Category 1</text><text x="83" y="122">Category 2</text><text x="125" y="122">Category 3</text><text x="167" y="122">Category 4</text></g>
  </svg>
  <div class="ico navy" style="left:262px;top:72px;width:26px;height:26px;border:2px solid #fff;box-shadow:0 0 0 1.5px var(--navy)"><svg viewBox="0 0 10 10"><circle cx="5" cy="5" r="3.8" fill="none" stroke="#fff"/><path d="M5 2.6V5h2" stroke="#fff" fill="none"/></svg></div>
  <div class="ico yellow" style="left:262px;top:118px;width:26px;height:26px"><svg viewBox="0 0 10 10"><rect x="1.5" y="2.5" width="7" height="4.5" fill="none" stroke="#fff"/><rect x="3" y="7.5" width="4" height="1" fill="#fff"/></svg></div>
  <div class="ico teal" style="left:262px;top:164px;width:26px;height:26px"><svg viewBox="0 0 10 10"><circle cx="3" cy="4" r="1.4" fill="#fff"/><circle cx="7" cy="4" r="1.4" fill="#fff"/><circle cx="5" cy="3.4" r="1.6" fill="#fff"/><path d="M1 8c0-2 8-2 8 0z" fill="#fff"/></svg></div>
  <div class="abs" style="left:298px;top:72px;width:120px"><div class="h9">Option <b>One</b></div><div class="body5">Short note on this point.</div></div>
  <div class="abs" style="left:298px;top:118px;width:120px"><div class="h9">Option <b>Two</b></div><div class="body5">Short note on this point.</div></div>
  <div class="abs" style="left:298px;top:164px;width:120px"><div class="h9">Option <b>Three</b></div><div class="body5">Short note on this point.</div></div>
  <div class="foot-brand"><span class="dot"></span>Solvexa</div><div class="foot-copy">© 2022 Solvexa. All rights reserved.</div><div class="foot-page">17</div>
</div>

<div class="slide" style="left:456px;top:1062px">
  <div class="abs" style="left:210px;top:0;width:244px;height:238px;border-radius:130px 0 0 130px/238px 0 0 0;background:linear-gradient(160deg,#2b4563 0%,#6d8aa4 40%,#c9d5df 70%,#3c5670 100%)" role="img" aria-label="Photo looking up at glass office towers"></div>
  <div class="ts-accent" style="left:412px;top:140px;width:50px;height:88px"></div>
  <div class="abs" style="left:32px;top:98px;display:flex;align-items:center;gap:7px;font-size:24px;font-weight:500;color:var(--navy)"><span style="width:17px;height:17px;border-radius:50%;background:var(--yellow)"></span>Solvexa</div>
  <div class="abs" style="left:32px;top:152px;font-size:8px;font-weight:700;color:var(--navy)">Contact Us</div>
  <div class="abs" style="left:32px;top:168px;font-size:5px;color:var(--grey);line-height:2.2">
    <div><svg width="6" height="6" viewBox="0 0 10 10" style="vertical-align:middle;margin-right:5px"><path d="M2 1l2 2-1 1.5c1 2 2 3 3 3L7.5 6l2 2-1.5 1.5C4 9 1 6 .5 1.5z" fill="var(--navy)"/></svg>Phone Number Goes Here</div>
    <div><svg width="6" height="6" viewBox="0 0 10 10" style="vertical-align:middle;margin-right:5px"><rect x="1" y="2" width="8" height="6" fill="none" stroke="var(--navy)"/><path d="M1 2l4 3 4-3" fill="none" stroke="var(--navy)"/></svg>E-Mail Address Goes Here</div>
    <div><svg width="6" height="6" viewBox="0 0 10 10" style="vertical-align:middle;margin-right:5px"><circle cx="5" cy="5" r="4" fill="none" stroke="var(--navy)"/><path d="M1 5h8M5 1c-2 2-2 6 0 8M5 1c2 2 2 6 0 8" fill="none" stroke="var(--navy)"/></svg>URL Address Goes Here</div>
  </div>
  <div class="ts-foot teal">© 2022 Solvexa. All rights reserved.</div>
</div>

</body>
</html>
```